Veltrano.co - Polar Expeditions Specialists

We need a modern, visually striking business card for Veltrano.co, a company specialized in selling expedition cruises to the most remote regions on Earth, with a focus on the Arctic and Antarctica. The design should instantly communicate that the cardholder is an expert in polar travel. Use clean, premium aesthetics with cool tones like icy blue and white, possibly incorporating polar imagery (ice, glaciers, penguins, etc.)

Attached the logo

Contact Information for Business Card

Feels high-end and trustworthy.. Visually memorable — encourages people to keep it

Colors
0054AA
0677BA
7BADD7
CADEEF
E8F1F8

Requirements
Must have
• ice, glaciers, penguins, montains
Nice to have
• modern, transparente,

```html
<!DOCTYPE html>
<html lang="en">
<head>
<meta charset="utf-8">
<title>Veltrano.co – Business Card</title>
<link href="https://fonts.googleapis.com/css2?family=Poppins:wght@400;500;700&display=swap" rel="stylesheet">
<style>
  :root {
    --stage: #3b3b3b;
    --card: #151515;
    --brand-blue: #3a7fcf;
    --edge-blue: #2f74c8;
    --text-white: #f2f2f2;
    --mark-grey: #8c8c8c;
    --tag-grey: #4a4a4a;
  }
  * { margin: 0; padding: 0; box-sizing: border-box; }
  html, body { width: 1200px; height: 791px; overflow: hidden; }
  body {
    background: var(--stage);
    font-family: "Poppins", sans-serif;
    position: relative;
  }
  .card {
    position: absolute;
    top: 235px;
    width: 540px;
    height: 310px;
    background: var(--card);
    border-bottom: 3px solid var(--edge-blue);
    box-shadow: 0 14px 30px rgba(0,0,0,.45);
    overflow: hidden;
  }
  .card--front { left: 40px; }
  .card--back { left: 620px; }

  /* front */
  .front-brand {
    position: absolute;
    left: 30px;
    top: 132px;
    width: 245px;
    display: flex;
    align-items: center;
    gap: 12px;
  }
  .brand-dot {
    width: 38px; height: 38px;
    border-radius: 50%;
    background: var(--brand-blue);
    flex: none;
  }
  .brand-name {
    font-weight: 700;
    font-size: 28px;
    line-height: 1;
    color: var(--brand-blue);
    white-space: nowrap;
  }
  .brand-tagline {
    font-weight: 500;
    font-size: 10px;
    color: var(--brand-blue);
    margin-top: 6px;
    letter-spacing: .2px;
    white-space: nowrap;
  }
  .front-divider {
    position: absolute;
    left: 292px;
    top: 70px;
    width: 2px;
    height: 170px;
    background: var(--edge-blue);
  }
  .contact {
    position: absolute;
    left: 316px;
    top: 78px;
    width: 210px;
  }
  .contact-name {
    font-weight: 700;
    font-size: 19px;
    color: var(--brand-blue);
    letter-spacing: .3px;
    white-space: nowrap;
  }
  .contact-role {
    font-size: 14px;
    color: var(--text-white);
    margin-bottom: 20px;
  }
  .contact-line {
    display: flex;
    align-items: center;
    gap: 8px;
    font-size: 12.5px;
    color: var(--text-white);
    margin-bottom: 7px;
    white-space: nowrap;
  }
  .contact-line svg { width: 12px; height: 12px; flex: none; }

  /* back */
  .back-brand {
    position: absolute;
    left: 0; right: 0;
    top: 112px;
    display: flex;
    justify-content: center;
    align-items: center;
    gap: 16px;
  }
  .back-brand .brand-dot { width: 56px; height: 56px; background: #0b0b0b; }
  .back-brand .brand-name { font-size: 44px; color: var(--mark-grey); }
  .back-brand .brand-tagline { font-size: 13px; color: var(--tag-grey); }
</style>
</head>
<body>

  <section class="card card--front">
    <div class="front-brand">
      <span class="brand-dot"></span>
      <div>
        <div class="brand-name">Veltrano.co</div>
        <div class="brand-tagline">Polar Expeditions Specialists</div>
      </div>
    </div>

    <div class="front-divider"></div>

    <div class="contact">
      <div class="contact-name">MARCUS RENDELL</div>
      <div class="contact-role">President</div>
      <div class="contact-line">
        <svg viewBox="0 0 12 12"><path d="M3 1l2 2.5-1.2 1.2a6 6 0 0 0 3.5 3.5L8.5 7 11 9l-1.2 2C5.5 11 1 6.5 1 2.2z" fill="var(--brand-blue)"/></svg>
        555-310-4872
      </div>
      <div class="contact-line">
        <svg viewBox="0 0 12 12"><rect x="1" y="2.5" width="10" height="7" rx="1" fill="var(--brand-blue)"/><path d="M1.5 3l4.5 3.5L10.5 3" stroke="var(--card)" fill="none"/></svg>
        marcusrendell@veltrano.co
      </div>
      <div class="contact-line">
        <svg viewBox="0 0 12 12"><circle cx="6" cy="6" r="5" fill="var(--brand-blue)"/><path d="M1 6h10M6 1c2 2.5 2 7.5 0 10M6 1c-2 2.5-2 7.5 0 10" stroke="var(--card)" stroke-width=".8" fill="none"/></svg>
        www.veltrano.co
      </div>
    </div>
  </section>

  <section class="card card--back">
    <div class="back-brand">
      <span class="brand-dot"></span>
      <div>
        <div class="brand-name">Veltrano.co</div>
        <div class="brand-tagline">Polar Expeditions Specialists</div>
      </div>
    </div>
  </section>

</body>
</html>
```